Business Card Design Project for an English Teacher

I need a business card design for my new job.
I'd like to start teaching English as a freelance.
My students will be children, teenager, and adults, who don't like or hesitate to study English and I would like to open a door to the new world for them.

I'd like to put the information below;
[right side]
1. name
2. mail address
3. mobile number
4. website or facebook page

[back]
1.my message: Feel free at asking me anything about my classes

2.lesson list such as:
price: 3150 yen ~

calsses:
kids class( mum& dad can join) ... 30 minutes / 45 minutes
students (over age 13).... 60minutes / 90 minutes
Adult (over age 19) .... 60 minutes / 90 minutes

3. I'll have both Web Lesson and Face to Face Lesson

4. Free trial lesson

Target Market(s)

My students will be children, teenager, and adults, who don't like or hesitate to study English

Industry/Entity Type

Business

Requirements
Must have
• designed both side

```html
<!DOCTYPE html>
<html lang="en">
<head>
<meta charset="utf-8">
<title>Open Door English – Business Card</title>
<link rel="stylesheet" href="https://fonts.googleapis.com/css2?family=Arimo:wght@400;700&family=Questrial&display=swap">
<style>
  :root {
    --purple: #6e3f75;
    --purple-text: #6a3a70;
    --blue: #1b6fb8;
    --green: #1fa347;
    --white: #ffffff;
    --backdrop: #e6e6e6;
    --shadow: rgba(0,0,0,0.35);
  }
  * { margin: 0; padding: 0; box-sizing: border-box; }
  html, body { width: 1200px; height: 900px; overflow: hidden; }
  body { background: var(--backdrop); position: relative; font-family: "Arimo", Arial, sans-serif; }

  .card {
    position: absolute;
    border-radius: 14px;
    overflow: hidden;
    box-shadow: 2px 4px 8px var(--shadow);
  }

  /* Front */
  .card-front { left: 103px; top: 72px; width: 615px; height: 336px; background: var(--white); color: var(--purple-text); }
  .brand { position: absolute; left: 38px; top: 52px; display: flex; align-items: center; gap: 12px; }
  .brand-mark { width: 26px; height: 26px; background: var(--purple); }
  .brand-name { font-weight: 700; font-size: 34px; letter-spacing: 1px; color: var(--purple); }
  .divider { position: absolute; left: 40px; top: 134px; width: 538px; height: 2px; background: var(--purple); }
  .person-name { position: absolute; left: 37px; top: 166px; font-size: 44px; font-weight: 700; line-height: 1; }
  .person-role { position: absolute; left: 38px; top: 211px; font-size: 15px; }

  .contact-list { position: absolute; list-style: none; font-size: 12.5px; }
  .contact-list li { display: flex; align-items: center; gap: 11px; height: 19px; }
  .contact-primary { left: 36px; top: 251px; font-size: 13.5px; }
  .contact-social { left: 240px; top: 240px; }
  .icon { width: 14px; height: 14px; flex: none; }

  .strip { position: absolute; bottom: 0; height: 8px; }
  .front-green { left: 259px; width: 24px; background: var(--green); }
  .front-blue { left: 283px; width: 24px; background: var(--blue); }
  .front-purple { left: 307px; right: 0; background: var(--purple); }

  /* Back */
  .card-back { left: 483px; top: 482px; width: 617px; height: 338px; background: var(--purple); color: var(--white); font-family: "Questrial", "Century Gothic", sans-serif; }
  .quote-mark { position: absolute; font-family: Georgia, "Times New Roman", serif; font-size: 82px; font-weight: 700; line-height: 1; }
  .quote-open { left: 56px; top: 32px; }
  .quote-close { left: 368px; top: 76px; }
  .message { position: absolute; left: 114px; top: 50px; font-size: 27px; line-height: 33px; }
  .back-rule { position: absolute; left: 60px; top: 138px; width: 498px; height: 1px; background: var(--white); }
  .price { position: absolute; right: 59px; top: 143px; font-size: 16px; }
  .classes-title { position: absolute; left: 79px; top: 160px; font-size: 24px; }
  .class-list { position: absolute; left: 80px; top: 194px; list-style: none; font-size: 14.5px; }
  .class-list li { display: grid; grid-template-columns: 265px 28px auto; height: 22px; align-items: center; }
  .class-name::before { content: "\2605"; margin-right: 6px; font-size: 13px; }
  .lesson-types { position: absolute; left: 0; right: 0; top: 277px; text-align: center; font-size: 12px; word-spacing: 1px; }

  .back-white { left: 0; width: 308px; height: 10px; background: var(--white); }
  .back-blue { left: 308px; width: 24px; height: 10px; background: var(--blue); }
  .back-green { left: 332px; width: 24px; height: 10px; background: var(--green); }
</style>
</head>
<body>

<section class="card card-front" aria-label="Business card front">
  <div class="brand">
    <span class="brand-mark"></span>
    <span class="brand-name">Open Door English</span>
  </div>
  <div class="divider"></div>
  <h1 class="person-name">Mika Harada</h1>
  <p class="person-role">English Instructor</p>

  <ul class="contact-list contact-primary">
    <li>
      <svg class="icon" viewBox="0 0 14 14" aria-hidden="true"><circle cx="7" cy="7" r="7" fill="#6e3f75"/><path d="M4.3 3.6l1.4-.3.7 1.8-.9.7c.4.9 1 1.6 1.9 2l.7-.9 1.8.7-.3 1.4c-3 .2-5.5-2.3-5.3-5.4z" fill="#fff"/></svg>
      090-4821-3067
    </li>
    <li>
      <svg class="icon" viewBox="0 0 14 14" aria-hidden="true"><circle cx="7" cy="7" r="7" fill="#6e3f75"/><rect x="3.5" y="4.5" width="7" height="5" fill="#fff"/><path d="M3.5 4.5L7 7.3l3.5-2.8" stroke="#6e3f75" stroke-width=".8" fill="none"/></svg>
      mikaharada@mailbox.com
    </li>
  </ul>

  <ul class="contact-list contact-social">
    <li><svg class="icon" viewBox="0 0 14 14" aria-hidden="true"><circle cx="7" cy="7" r="7" fill="#6e3f75"/></svg>mikaharada@talkline.com</li>
    <li><svg class="icon" viewBox="0 0 14 14" aria-hidden="true"><circle cx="7" cy="7" r="7" fill="#6e3f75"/></svg>mikaharada@circlepage.com</li>
    <li><svg class="icon" viewBox="0 0 14 14" aria-hidden="true"><circle cx="7" cy="7" r="7" fill="#6e3f75"/></svg>www.mikaharada.com</li>
  </ul>

  <span class="strip front-green"></span>
  <span class="strip front-blue"></span>
  <span class="strip front-purple"></span>
</section>

<section class="card card-back" aria-label="Business card back">
  <span class="quote-mark quote-open">&ldquo;</span>
  <p class="message">Feel free at asking me anything<br>about my classes</p>
  <span class="quote-mark quote-close">&rdquo;</span>
  <div class="back-rule"></div>
  <p class="price">Price: 3,150 yen</p>
  <h2 class="classes-title">Classes:</h2>
  <ul class="class-list">
    <li><span class="class-name">Kids Class (Mom &amp; Dad can join)</span><span>-</span><span>30 minutes / 45 minutes</span></li>
    <li><span class="class-name">Students (over age 13)</span><span>-</span><span>60minutes / 90 minutes</span></li>
    <li><span class="class-name">Adult (over age 19)</span><span>-</span><span>60 minutes / 90 minutes</span></li>
  </ul>
  <p class="lesson-types">Web Lesson &nbsp;|&nbsp; Face to Face Lesson &nbsp;|&nbsp; Free Trial Lesson</p>

  <span class="strip back-white"></span>
  <span class="strip back-blue"></span>
  <span class="strip back-green"></span>
</section>

</body>
</html>
```